Marwick Family Chiropractic Stationary

The letterhead and business card must have our logo.
We would like to see the logo used in different ways ( It can be expanded upon in the stationary.)
Please use the the same or similar colors.
Must be eye catching and memorable.
Must be easy to read

Reason: The doctor has been too busy to make any final decisions. He would like to give himself a little more time.

Target Market(s)

Chiropractic Healthcare

Industry/Entity Type

Business

Requirements
Must have
• Dr. Leonard Marwick D.C.
Chiropractor

207-555-0183

417 Birchfield Road, Suite 3
Halden, ME 04091

drmarwick@marwickspine.example
www.marwickspine.example
www.facebook.com/MarwickFamilySpine
Should not have
• should not be difficult to read

```html
<!DOCTYPE html>
<html lang="en">
<head>
<meta charset="utf-8">
<title>Marwick Family Chiropractic – Stationery</title>
<link rel="stylesheet" href="https://fonts.googleapis.com/css2?family=Questrial&display=swap">
<style>
  :root {
    --backdrop: #e4e4e2;
    --paper: #fbfbfa;
    --paper-edge: #d9d9d6;
    --brand-green: #2f9e3a;
    --leaf-olive: #a8a21e;
    --ink: #3a3a3a;
    --ink-soft: #777;
    --flap-grey: #a9a9a9;
    --card-back: #b5b5b4;
  }
  * { box-sizing: border-box; margin: 0; padding: 0; }
  html, body { width: 1200px; height: 808px; overflow: hidden; }
  body {
    background: var(--backdrop);
    font-family: "Questrial", "Century Gothic", sans-serif;
    color: var(--ink);
    position: relative;
  }
  .sheet {
    position: absolute;
    background: var(--paper);
    box-shadow: 0 2px 8px rgba(0,0,0,.18);
  }

  /* Stacked name lockup: one colour, one weight */
  .brand-name {
    color: var(--brand-green);
    font-weight: 400;
    text-transform: uppercase;
    line-height: 1;
    display: flex;
    flex-direction: column;
    align-items: flex-start;
  }
  .brand-name .name-main { font-size: 28px; letter-spacing: 2px; }
  .brand-name .name-sub { font-size: 9px; letter-spacing: .6px; margin-top: 3px; }

  .brand-mark {
    position: absolute;
    display: flex;
    align-items: center;
    justify-content: center;
    text-align: center;
    color: var(--brand-green);
  }
  .brand-mark span::before {
    content: "";
    display: block;
    margin: 0 auto 8px;
    border-radius: 50%;
    background: var(--brand-green);
  }
  .contact { font-size: 9px; color: var(--ink-soft); line-height: 1.6; }
  .contact li { list-style: none; display: flex; align-items: center; gap: 4px; white-space: nowrap; }
  .contact svg { width: 8px; height: 8px; fill: var(--leaf-olive); flex: none; }
  .web { position: absolute; font-size: 8px; color: var(--ink-soft); }

  /* Letterhead */
  .letterhead { left: 20px; top: 20px; width: 580px; height: 768px; }
  .letterhead .brand-name { position: absolute; left: 30px; top: 92px; }
  .letterhead .contact { position: absolute; right: 40px; top: 36px; }
  .letterhead .brand-mark { right: 40px; bottom: 40px; width: 170px; height: 150px; font-size: 22px; }
  .letterhead .brand-mark span::before { width: 34px; height: 34px; }
  .letterhead .web { left: 30px; bottom: 24px; }

  /* Business card */
  .card-front { left: 630px; top: 30px; width: 260px; height: 150px; padding: 14px 16px; }
  .card-front .doctor { color: var(--brand-green); font-size: 12px; }
  .card-front .role { font-size: 8px; color: var(--ink-soft); margin-bottom: 18px; }
  .card-front .brand-name { margin-bottom: 5px; }
  .card-front .brand-name .name-main { font-size: 17px; letter-spacing: 1px; }
  .card-front .brand-name .name-sub { font-size: 6px; margin-top: 2px; }
  .card-front .contact { font-size: 6.5px; line-height: 1.5; }
  .card-front .contact svg { width: 6px; height: 6px; }
  .card-front .brand-mark { right: 10px; bottom: 14px; width: 80px; height: 80px; font-size: 11px; }
  .card-front .brand-mark span::before { width: 22px; height: 22px; margin-bottom: 5px; }
  .card-back { left: 910px; top: 30px; width: 260px; height: 150px; background: var(--card-back); }
  .card-back .brand-mark { left: 0; right: 0; top: 28px; height: 70px; font-size: 12px; color: #fff; }
  .card-back .brand-mark span::before { width: 22px; height: 22px; background: #fff; margin-bottom: 5px; }
  .card-back .web { left: 0; right: 0; bottom: 14px; text-align: center; color: #f3f3f3; }

  /* Envelope front */
  .envelope-front { left: 630px; top: 205px; width: 550px; height: 240px; }
  .envelope-front .brand-name { position: absolute; left: 34px; top: 38px; }
  .envelope-front .brand-name .name-main { font-size: 26px; }
  .address-window {
    position: absolute; left: 34px; top: 100px; width: 270px; height: 95px;
    border: 1px solid var(--paper-edge); border-radius: 12px;
    background: #f3f3f2;
  }
  .envelope-front .brand-mark { right: 30px; top: 60px; width: 150px; height: 130px; font-size: 20px; }
  .envelope-front .brand-mark span::before { width: 30px; height: 30px; }
  .envelope-front .web { left: 34px; bottom: 16px; }

  /* Envelope back */
  .envelope-back { left: 630px; top: 470px; width: 550px; height: 318px; overflow: hidden; }
  .envelope-back .flap { position: absolute; inset: 0; width: 100%; height: 100%; }
  .envelope-back .brand-mark { left: 0; right: 0; top: 40px; height: 60px; font-size: 11px; }
  .envelope-back .brand-mark span::before { width: 18px; height: 18px; margin-bottom: 5px; }
  .envelope-back .contact { position: absolute; right: 40px; bottom: 30px; }
</style>
</head>
<body>

<svg width="0" height="0" style="position:absolute">
  <symbol id="icon-pin" viewBox="0 0 10 10"><path d="M5 0a3.5 3.5 0 0 0-3.5 3.5C1.5 6 5 10 5 10s3.5-4 3.5-6.5A3.5 3.5 0 0 0 5 0zm0 5a1.5 1.5 0 1 1 0-3 1.5 1.5 0 0 1 0 3z"/></symbol>
  <symbol id="icon-phone" viewBox="0 0 10 10"><path d="M2 0l2 2.5-1 1.2c.6 1.3 1.6 2.3 2.9 2.9l1.1-1 2.5 2L8.3 10C4 9.6.4 6 0 1.7z"/></symbol>
  <symbol id="icon-mail" viewBox="0 0 10 10"><path d="M0 2h10v6H0zm1 1v.3l4 2.5 4-2.5V3z"/></symbol>
</svg>

<section class="sheet letterhead">
  <div class="contact">
    <ul>
      <li><svg><use href="#icon-pin"/></svg>417 Birchfield Road, Suite 3 Halden, ME 04091</li>
      <li><svg><use href="#icon-phone"/></svg>207-555-0183 <svg><use href="#icon-mail"/></svg>drmarwick@marwickspine.example</li>
    </ul>
  </div>
  <h1 class="brand-name"><span class="name-main">Marwick</span><span class="name-sub">Family Chiropractic</span></h1>
  <div class="brand-mark"><span>Marwick</span></div>
  <p class="web">www.marwickspine.example</p>
</section>

<section class="sheet card-front">
  <p class="doctor">Dr. Leonard Marwick D.C.</p>
  <p class="role">Chiropractor</p>
  <p class="brand-name"><span class="name-main">Marwick</span><span class="name-sub">Family Chiropractic</span></p>
  <ul class="contact">
    <li><svg><use href="#icon-pin"/></svg>417 Birchfield Road, Suite 3</li>
    <li><svg><use href="#icon-pin"/></svg>Halden, ME 04091</li>
    <li><svg><use href="#icon-phone"/></svg>207-555-0183</li>
    <li><svg><use href="#icon-mail"/></svg>drmarwick@marwickspine.example</li>
  </ul>
  <div class="brand-mark"><span>Marwick</span></div>
</section>

<section class="sheet card-back">
  <div class="brand-mark"><span>Marwick</span></div>
  <p class="web">www.marwickspine.example</p>
</section>

<section class="sheet envelope-front">
  <p class="brand-name"><span class="name-main">Marwick</span><span class="name-sub">Family Chiropractic</span></p>
  <div class="address-window"></div>
  <div class="brand-mark"><span>Marwick</span></div>
  <p class="web">www.marwickspine.example</p>
</section>

<section class="sheet envelope-back">
  <svg class="flap" viewBox="0 0 550 318" preserveAspectRatio="none">
    <path d="M0 0h550v30L290 150Q275 158 260 150L0 30z" fill="var(--flap-grey)"/>
    <path d="M0 318L250 170M550 318L300 170" stroke="var(--paper-edge)" stroke-width="1" fill="none"/>
  </svg>
  <div class="brand-mark"><span>Marwick</span></div>
  <div class="contact">
    <ul>
      <li><svg><use href="#icon-pin"/></svg>417 Birchfield Road, Suite 3 Halden, ME 04091</li>
      <li><svg><use href="#icon-phone"/></svg>207-555-0183 <svg><use href="#icon-mail"/></svg>drmarwick@marwickspine.example</li>
    </ul>
  </div>
</section>

</body>
</html>
```